IV Nutritional Clinic Web Design

We are working with Velqo. They are an IV Nutritional Clinic and in need of a new website design.
Some sites to use for inspiration:
https://brightpathcareco.com
https://www.ourzavrowellness.com
https://www.dewspringlounge.com
https://qvitalsurge.com
https://www.lumo-vital.com/pages/iv-therapy-west-hollywood
https://www.tqoncologyhub.com/cancer-care/iv-drips/
https://dripwellary.com
https://corvinahealthhub.com
Thank you for taking the time to consider designing a website for us. We are web developers based in Stockton, CA, USA. Most of our projects go through the same process. Understanding this process may help you win a project with us. We custom-code all of our websites in-house. We don’t have any requirements as to what tools you use for your design, but we prefer Figma files. For any design that we label as four-stars, we send it to the client for review. The client picks the final design they want us to use. Once we complete this process, we will continue to show additional clients all the four-star sites and purchase them later. Your designs will have multiple chances to sell. For better chances of success, we ask that you follow these guidelines.
IMAGES:
If you use any images or icons in the design, we ask that you have a link to the asset so we can purchase the image/icon. Most of the designs we submit do not have the customer’s images on them unless they have some great images. Be creative; show us the feeling you are trying to portray with your image choices. Use any royalty-free site you choose. We subscribe to Pixvane and mainly use their images, but we can purchase images outside of Pixvane.
PLEASE NOTE: we will not submit designs to clients with watermarks on the images.
FONTS:
We ask that you identify the fonts used in the design. This can be done in a message if you want. We typically use Google Fonts and Pixvane Fonts.
CONTENT:
We're always open to different content and ideas. We often submit designs with stock images so the client can see our vision. We typically take pictures after the website launch to use their images with our vision. Lorem Ipsum is fine for paragraphs, but we ask that you write the headers in correct English. We want to be able to show the vision and identify the sections of the website.
INSPIRATION:
We typically add a couple of links in the brief of websites we like to help you get started in your design.
REVISIONS:
We do not often ask for revisions of the designs unless we see something in the design that may not appeal to the client. If there are slight changes that we want to make, we do that in the development process.
FEEDBACK:
We rarely give feedback on designs during the design process. We are working on many website projects and do not have the time to provide feedback. We usually respond if your request is well thought out and asks specific questions, but a note asking “feedback, please” usually goes unanswered.

```html
<!DOCTYPE html>
<html lang="en">
<head>
<meta charset="utf-8">
<title>Velqo — IV Nutritional Clinic</title>
<link href="https://fonts.googleapis.com/css2?family=Poppins:wght@400;500;600;700&display=swap" rel="stylesheet">
<style>
:root{
  --navy:#1d2a8c;
  --navy-dark:#17237a;
  --green:#7aab3e;
  --ink:#1b2450;
  --muted:#6c7390;
  --sky:#eef5fc;
  --line:#d9e6c6;
  --white:#ffffff;
  --stage:#eceef1;
}
*{box-sizing:border-box;margin:0;padding:0}
html,body{width:1200px;height:1200px;overflow:hidden}
body{background:var(--stage);font-family:'Poppins',sans-serif;color:var(--ink);position:relative}
.page{position:absolute;left:443px;top:3px;width:640px;transform:scale(.49);transform-origin:top left;background:var(--white);box-shadow:0 10px 40px rgba(20,30,80,.18)}
.wrap{padding:0 80px}
.btn{display:inline-flex;align-items:center;gap:6px;background:var(--green);color:var(--white);font-size:7px;font-weight:600;letter-spacing:.3px;padding:7px 13px;border-radius:3px;text-transform:uppercase}
.btn i{width:8px;height:8px;border:1.5px solid var(--white);border-radius:1.5px;display:block}
.eyebrow{font-size:5.5px;font-weight:600;color:var(--green);text-transform:uppercase;letter-spacing:.3px}
.title{font-size:19px;font-weight:700;color:var(--navy);line-height:1.2}
.body-copy{font-size:6.5px;color:var(--muted);line-height:1.75}
.link{font-size:5.5px;font-weight:600;color:var(--navy);text-transform:uppercase;border-bottom:1px solid currentColor;padding-bottom:1px}
.social{display:flex;gap:5px}
.social span{width:14px;height:14px;border:1px solid var(--navy);border-radius:50%;display:block}

/* header */
.topbar{height:25px;display:flex;align-items:center;justify-content:space-between;padding:0 32px;font-size:6.5px;color:var(--navy)}
.topbar .phone{display:flex;align-items:center;gap:4px}
.nav{height:44px;display:flex;align-items:center;justify-content:space-between;padding:0 32px;border-top:1px solid #eef0f4}
.brand{font-size:19px;font-weight:700;color:var(--navy);letter-spacing:1px}
.menu{display:flex;gap:17px;font-size:7px;color:var(--navy);margin-left:120px}
/* hero */
.hero{height:350px;position:relative;background:linear-gradient(180deg,#f4f8fd 0%,#dcebf7 55%,#bcd7ee 100%);overflow:hidden}
.hero-copy{position:absolute;left:80px;top:98px;width:240px}
.hero-copy h1{font-size:32px;font-weight:700;color:var(--navy);line-height:1.17;margin:6px 0 10px}
.hero-copy p{font-size:7px;font-weight:500;color:var(--navy);line-height:1.7;margin-bottom:14px}
.hero-media{position:absolute;right:32px;top:8px;width:175px;height:330px;border-radius:30px 30px 20px 20px;background:linear-gradient(160deg,#e7eef6,#b8d0e6 45%,#9fbcd8)}
/* intro */
.intro{height:475px;background:var(--sky);position:relative}
.features{position:absolute;left:80px;top:49px;display:flex;gap:7px}
.feature{width:155px;height:115px;border-radius:5px;background:var(--navy);color:var(--white);padding:22px 14px 0 60px;position:relative}
.feature.alt{background:var(--green)}
.feature .ico{position:absolute;left:18px;top:22px;width:32px;height:32px;border-radius:50%;background:var(--white)}
.feature h3{font-size:10px;font-weight:500;margin-bottom:5px}
.feature p{font-size:6px;line-height:1.8;margin-bottom:5px}
.feature .link{color:var(--white);font-size:5px}
.portrait{position:absolute;left:120px;top:180px;width:170px;height:295px;border-radius:80px 80px 0 0;background:linear-gradient(180deg,#d7e3ef,#2aa6b5 55%,#1a8f9e)}
.about{position:absolute;left:350px;top:210px;width:210px}
.about .title{margin:3px 0 10px}
.facts{display:flex;gap:10px;margin:18px 0 19px}
.fact{width:97px;height:52px;border-radius:4px;background:#e2ebf5;display:flex;align-items:center;gap:6px;padding:0 12px;font-size:6px;color:var(--navy);line-height:1.6}
.tick{width:11px;height:11px;flex:none}
.btn.wide{width:164px;justify-content:center;font-size:5.5px;padding:6px}
/* services */
.services{height:288px;padding-top:42px}
.head-row{display:flex;justify-content:space-between;align-items:flex-end}
.arrows{display:flex;gap:7px}
.arrows span{width:25px;height:21px;border:1px solid var(--line);border-radius:4px;display:flex;align-items:center;justify-content:center;font-size:9px;color:var(--navy)}
.service-row{display:flex;gap:7px;margin-top:54px}
.service{width:155px;height:115px;border:1.5px solid var(--line);border-radius:5px;text-align:center;padding:26px 12px 0;position:relative}
.service .ico{position:absolute;top:-17px;left:61px;width:32px;height:32px;border-radius:50%;background:var(--green);border:4px solid #eef5e4}
.service h3{font-size:9px;font-weight:500;color:var(--navy);margin-bottom:5px}
.service p{margin-bottom:5px;font-size:6px}
.service .link{font-size:5px}
/* consult */
.consult{height:310px;position:relative;background:linear-gradient(180deg,var(--navy) 0 198px,var(--sky) 198px)}
.consult-copy{text-align:center;padding-top:36px;color:var(--white)}
.consult-copy h2{font-size:17px;font-weight:700;line-height:1.3;margin:4px 0 10px}
.consult-copy p{font-size:6.5px;line-height:1.8;color:#dfe4f7}
.doctors{position:absolute;left:32px;top:150px;display:flex;gap:9px}
.doctor{width:284px;height:151px;border-radius:3px;position:relative;background:linear-gradient(120deg,#ececec,#d6d6d6)}
.doctor-two{background:linear-gradient(120deg,#eaeaea,#c9cbd0)}
.doctor .tag{position:absolute;left:4px;bottom:4px;width:90px;height:82px;background:var(--green);border-radius:3px;color:var(--white);font-size:6px;font-weight:600;text-align:center;padding-top:22px;line-height:1.6}
.doctor .tag b{display:block;width:16px;height:16px;border-radius:50%;background:var(--white);margin:6px auto 0;position:relative}
.doctor .tag b:after{content:"";position:absolute;left:6px;top:4px;border-left:6px solid var(--green);border-top:4px solid transparent;border-bottom:4px solid transparent}
/* testimonials */
.testimonials{height:287px;background:var(--sky);padding-top:14px}
.quotes{display:flex;gap:7px;margin-top:20px}
.quote{width:155px;height:146px;background:var(--white);border-radius:4px;padding:12px 14px}
.quote .top{display:flex;justify-content:space-between;align-items:center;color:var(--navy);margin-bottom:6px}
.quote .mark{font-size:26px;font-weight:700;line-height:.6;height:14px}
.quote .stars{font-size:7px;color:var(--green);letter-spacing:1.5px}
.quote p{font-size:5.5px;color:var(--muted);line-height:2;margin-bottom:20px}
.quote h4{font-size:6px;font-weight:600;color:var(--navy)}
.quote small{font-size:5px;color:var(--navy);font-weight:500}
/* stats */
.stats{height:88px;background:var(--navy);display:flex;justify-content:center;gap:85px;align-items:center;color:var(--white);text-align:center}
.stat .ico{width:34px;height:34px;border:1.5px solid var(--white);border-radius:50%;margin:0 auto 4px}
.stat strong{display:block;font-size:10px;font-weight:500}
.stat small{font-size:6px;color:var(--green)}
/* articles */
.articles{height:385px;background:var(--white);padding-top:38px;text-align:center}
.articles .title{margin-top:2px}
.posts{display:flex;gap:7px;margin-top:24px;text-align:left}
.post{width:155px;height:197px;background:var(--white);box-shadow:0 2px 10px rgba(30,40,100,.08);border-radius:4px;overflow:hidden}
.post .thumb{height:102px;position:relative}
.post .chip{position:absolute;right:8px;top:8px;background:var(--white);color:var(--green);font-size:4.5px;font-weight:600;padding:3px 8px;border-radius:2px}
.post .in{padding:12px 14px}
.post h3{font-size:7.5px;font-weight:500;color:var(--navy);line-height:1.6;margin-bottom:8px}
.meta{display:flex;gap:12px;font-size:5px;color:var(--muted);margin-bottom:12px}
.meta span:before{content:"";display:inline-block;width:5px;height:5px;background:var(--green);border-radius:1px;margin-right:3px;vertical-align:-1px}
.btn.more{margin-top:27px;font-size:5px;padding:7px 15px}
/* footer */
.footer{height:185px;background:var(--navy);color:var(--white);display:flex;padding:56px 80px 0;gap:0}
.footer .col{font-size:5.5px;line-height:2;color:#dde2f6}
.footer h5{font-size:7.5px;font-weight:600;color:var(--white);margin-bottom:8px}
.footer .call{display:inline-flex;align-items:center;gap:4px;border:1px solid var(--white);border-radius:4px;padding:2px 8px;margin-top:6px;color:var(--white)}
.footer .social span{border-color:var(--white);width:17px;height:17px}
</style>
</head>
<body>
<main class="page">
  <header>
    <div class="topbar">
      <div class="phone"><svg width="7" height="7" viewBox="0 0 24 24"><path fill="#7aab3e" d="M6.6 10.8a15 15 0 006.6 6.6l2.2-2.2a1 1 0 011-.25 11.4 11.4 0 003.6.6 1 1 0 011 1V20a1 1 0 01-1 1A17 17 0 013 4a1 1 0 011-1h3.5a1 1 0 011 1 11.4 11.4 0 00.6 3.6 1 1 0 01-.25 1z"/></svg>(+12) 555 014 2290</div>
      <div class="social"><span></span><span></span><span></span></div>
    </div>
    <nav class="nav">
      <div class="brand">VELQO</div>
      <div class="menu"><span>Home</span><span>About</span><span>Services</span><span>Treatment</span><span>Contact</span></div>
      <span class="btn"><i></i>Appointment</span>
    </nav>
  </header>

  <section class="hero" role="img" aria-label="Light blue water background with splashes">
    <div class="hero-copy">
      <div class="eyebrow" style="color:var(--navy)">IV Nutritional Clinic</div>
      <h1>Revitalize with IV Therapy</h1>
      <p>Lorem ipsum is simply dummy text of the printing and typesetting industry. Lorem Ipsum has been</p>
      <span class="btn"><i></i>Appointment</span>
    </div>
    <div class="hero-media" role="img" aria-label="IV drip bag filled with fresh fruit slices in water"></div>
  </section>

  <section class="intro">
    <div class="features">
      <div class="feature"><span class="ico"></span><h3>Hydrate</h3><p>Lorem ipsum is simply dummy text of the printing</p><span class="link">Find a doctor →</span></div>
      <div class="feature alt"><span class="ico"></span><h3>Therapy</h3><p>Lorem ipsum is simply dummy text of the printing</p><span class="link">Find a doctor →</span></div>
      <div class="feature"><span class="ico"></span><h3>Infusion</h3><p>Lorem ipsum is simply dummy text of the printing</p><span class="link">Find a doctor →</span></div>
    </div>
    <div class="portrait" role="img" aria-label="Smiling nurse in teal scrubs with arms crossed"></div>
    <div class="about">
      <div class="eyebrow">About us</div>
      <h2 class="title">Welcome To<br>Velqo Hydration</h2>
      <p class="body-copy">Lorem ipsum is simply dummy text of the printing and typesetting industry. Lorem Ipsum has been the industry's standard dummy text ever</p>
      <div class="facts">
        <div class="fact"><svg class="tick" viewBox="0 0 12 12"><circle cx="6" cy="6" r="5" fill="none" stroke="#7aab3e"/><path d="M3.5 6.2l1.7 1.6 3.3-3.4" fill="none" stroke="#7aab3e"/></svg>20+ years of excellence</div>
        <div class="fact"><svg class="tick" viewBox="0 0 12 12"><circle cx="6" cy="6" r="5" fill="none" stroke="#7aab3e"/><path d="M3.5 6.2l1.7 1.6 3.3-3.4" fill="none" stroke="#7aab3e"/></svg>24 Hours Medical Service</div>
      </div>
      <span class="btn wide"><i></i>Book an appointment</span>
    </div>
  </section>

  <section class="services wrap">
    <div class="head-row">
      <div><div class="eyebrow">Departments</div><h2 class="title" style="font-size:17px">Explore Our Services</h2></div>
      <div class="arrows"><span>←</span><span>→</span></div>
    </div>
    <div class="service-row">
      <div class="service"><span class="ico"></span><h3>Immune Support</h3><p class="body-copy">Lorem ipsum is simply dummy text of the printing and typesetting industry. Lorem Ipsum has been the</p><span class="link">View more →</span></div>
      <div class="service"><span class="ico"></span><h3>Vitamin C IV Therapy</h3><p class="body-copy">Lorem ipsum is simply dummy text of the printing and typesetting industry. Lorem Ipsum has been the</p><span class="link">View more →</span></div>
      <div class="service"><span class="ico"></span><h3>NAD+ Therapy</h3><p class="body-copy">Lorem ipsum is simply dummy text of the printing and typesetting industry. Lorem Ipsum has been the</p><span class="link">View more →</span></div>
    </div>
  </section>

  <section class="consult">
    <div class="consult-copy">
      <div class="eyebrow">Benefits of consultation</div>
      <h2>Consult The Best Doctor<br>In The Department</h2>
      <p>Lorem ipsum is simply dummy text of the printing and<br>typesetting industry. Lorem Ipsum has been</p>
    </div>
    <div class="doctors">
      <div class="doctor" role="img" aria-label="Female doctor in white coat pointing"><div class="tag">SAY HELLO TO<br>DENTIST<b></b></div></div>
      <div class="doctor doctor-two" role="img" aria-label="Male doctor in navy scrubs with stethoscope"><div class="tag">SAY HELLO TO<br>DENTIST<b></b></div></div>
    </div>
  </section>

  <section class="testimonials wrap">
    <div class="head-row">
      <div><div class="eyebrow">Testimonials</div><h2 class="title" style="font-size:17px">What Our Patient Says</h2></div>
      <div class="arrows"><span>←</span><span>→</span></div>
    </div>
    <div class="quotes">
      <div class="quote"><div class="top"><span class="mark">“</span><span class="stars">★★★★★</span></div><p>“I wish the world could know the wonderful things that are happening on the Velqo Hydration, who have had an injury that cured soon.”</p><h4>RENA HOLT</h4><small>CUSTOMER SERVICE</small></div>
      <div class="quote"><div class="top"><span class="mark">“</span><span class="stars">★★★★★</span></div><p>“I wish the world could know the wonderful things that are happening on the Velqo Hydration, who have had an injury that cured soon.”</p><h4>RENA HOLT</h4><small>CUSTOMER SERVICE</small></div>
      <div class="quote"><div class="top"><span class="mark">“</span><span class="stars">★★★★★</span></div><p>“I wish the world could know the wonderful things that are happening on the Velqo Hydration, who have had an injury that cured soon.”</p><h4>RENA HOLT</h4><small>CUSTOMER SERVICE</small></div>
    </div>
  </section>

  <section class="stats">
    <div class="stat"><div class="ico"></div><strong>1.5 Crore+</strong><small>Satisfied Patients</small></div>
    <div class="stat"><div class="ico"></div><strong>2 Million+</strong><small>Doctor Appointments</small></div>
    <div class="stat"><div class="ico"></div><strong>200,000+</strong><small>Certified Experts</small></div>
  </section>

  <section class="articles wrap">
    <div class="eyebrow">Our blog</div>
    <h2 class="title" style="font-size:17px">Latest Articles</h2>
    <div class="posts">
      <article class="post"><div class="thumb" role="img" aria-label="Hand with IV line in hospital" style="background:linear-gradient(135deg,#2b8a96,#cfe4ea)"><span class="chip">HEALTHCARE</span></div><div class="in"><h3>Potential treatment for an Inflammatory blood disease</h3><div class="meta"><span>Lio Varden</span><span>May 14, 2022</span></div><span class="link">View more →</span></div></article>
      <article class="post"><div class="thumb" role="img" aria-label="Patient resting in bed by a window" style="background:linear-gradient(135deg,#c9cdd2,#8e969c)"><span class="chip">INFUSION</span></div><div class="in"><h3>Potential treatment for an Inflammatory blood disease</h3><div class="meta"><span>Lio Varden</span><span>May 14, 2022</span></div><span class="link">View more →</span></div></article>
      <article class="post"><div class="thumb" role="img" aria-label="Child resting on a colourful pillow" style="background:linear-gradient(135deg,#e7c9a8,#f0e06a)"><span class="chip">THERAPY</span></div><div class="in"><h3>Potential treatment for an Inflammatory blood disease</h3><div class="meta"><span>Lio Varden</span><span>May 14, 2022</span></div><span class="link">View more →</span></div></article>
    </div>
    <span class="btn more">More articles</span>
  </section>

  <footer class="footer">
    <div class="col" style="width:142px"><h5>Contact</h5>118 Larkmoor Avenue, Fenwick<br>NC 28210, USA<br>support@velqomail.com<br>(+22) 555 - 0188 - 300</div>
    <div class="col" style="width:100px"><h5>Explore</h5>Style Guide<br>Changelog<br>Licenses<br>Protected Page<br>404 Page</div>
    <div class="col" style="width:163px"><h5>Book An Appointment</h5>The Velqo staff members are<br>well trained professionals.<br><span class="call">☎ (+12) 555 014 2290</span></div>
    <div class="col"><h5>Social Media</h5><div class="social"><span></span><span></span><span></span></div>© 2025 Velqo Hydration</div>
  </footer>
</main>
</body>
</html>
```